Cocktail-Making Assistant App re-design

Ok boys and girls, here's the deal:
I have an android app which is almost complete, but needs a design overhaul.

The app is a standard cocktail-making assistant: gives you a list of cocktails and the ability to see which cocktail you can make out of those ingredients (drinks, fruit, etc) you have at home.

I've attached some general app flow, as well as detailed requirements/explanation presentation. Most of those things are just FYI, so that you know what it's about.

3 screens are the most important (main screen, cocktail view screen, ingredient view screen), meaning I will pick the design mostly based on ideas for those 3 things, with the fourth being a rather simple list (given on attached flow, third tier)
Some other screens are derived from that, with some minor changes on it, but you shouldn't care about that.

There are lots of other, non-explained things which I said nothing about only because they are (from design point of view) completely the same and would only make it seem more complicated.

I don't want to influence the colour scheme, but the app will be released under RedFig developer name (having a light colured red fig as a logo) so I suppose some brownish design, for example, will not really fit nicely. If you, however, have a killer which you are confident will prove me wrong, I'm looking forward to seeing it!

It should be a serious, elegant look (as opposed to cartoonish, but we are not aiming for a business look at all!), not cluttered with details, no clubbing themes, glitter and so on.

Test apk file available on request (Android 2.3+).

Edit: payment is now guaranteed
Also please note that currently, the favorite, "heart" button has a motion effect:
on click it flies out of the screen to the left (white heart) and comes back to the screen as a red heart. Take that into consideration, if it means anything to you.

Target Market(s)

Whoever you imagine would enjoy drinking cocktails

Industry/Entity Type

Business

Requirements
Must have
• Everything is said in the provided documentation - images say more than I could possibly write here.
Nice to have
• As said, most of the icons are a nice-to-have. Only those which are critically linked to the rest of the design must be provided. More details in the docs.
Should not have
• No cartoon look, No zillion colours

```html
<!DOCTYPE html>
<html lang="en">
<head>
<meta charset="utf-8">
<title>Cocktail Search – Main Screen</title>
<link rel="stylesheet" href="https://fonts.googleapis.com/css2?family=Quicksand:wght@400;500&display=swap">
<style>
  :root {
    --page-bg: #e6e7e9;
    --screen-bg: #f1f1f1;
    --screen-glow: #ffffff;
    --header-top: #6cbde0;
    --header-bottom: #c9e6f2;
    --header-text: #ffffff;
    --quote-text: #8c8c8c;
    --label-text: #555555;
    --icon-stroke: #6f6f6f;
    --tile-shaker: #dfcfa7;
    --tile-bar: #9de6cf;
    --tile-cocktails: #d4f4d3;
    --tile-favorites: #e0b7a5;
    --tile-shopping: #cfe3f3;
    --tile-featured: #d4ccd1;
  }
  * { box-sizing: border-box; margin: 0; padding: 0; }
  html, body {
    width: 1200px;
    height: 993px;
    overflow: hidden;
    background: var(--page-bg);
    font-family: "Quicksand", "Helvetica Neue", Arial, sans-serif;
  }
  .app-screen {
    position: absolute;
    left: 330px;
    top: 19px;
    width: 540px;
    height: 955px;
    background: radial-gradient(ellipse at 50% 50%, var(--screen-glow) 40%, var(--screen-bg) 80%);
  }
  .app-header {
    height: 88px;
    background: linear-gradient(to bottom, var(--header-top), var(--header-bottom));
    display: flex;
    align-items: center;
    justify-content: space-between;
    padding: 0 14px;
  }
  .app-title {
    color: var(--header-text);
    font-size: 35px;
    font-weight: 400;
    letter-spacing: 0.3px;
  }
  .header-button {
    width: 54px;
    height: 54px;
    border-radius: 50%;
    border: 3px solid var(--header-text);
    display: flex;
    align-items: center;
    justify-content: center;
  }
  .quote {
    color: var(--quote-text);
    font-size: 24px;
    line-height: 34px;
    text-align: center;
    font-weight: 400;
  }
  .quote-intro { margin: 44px 50px 0; }
  .quote-footer { margin: 52px 60px 0; }
  .menu-grid {
    margin: 36px 10px 0;
    display: grid;
    grid-template-columns: 255px 255px;
    grid-auto-rows: 157px;
    column-gap: 10px;
    row-gap: 8px;
  }
  .menu-tile {
    position: relative;
    display: flex;
    flex-direction: column;
    align-items: center;
    justify-content: flex-end;
    padding-bottom: 10px;
  }
  .menu-tile svg {
    position: absolute;
    left: 50%;
    top: 24px;
    transform: translateX(-50%);
  }
  .tile-label {
    color: var(--label-text);
    font-size: 20px;
    font-weight: 400;
  }
  .tile-shaker { background: var(--tile-shaker); }
  .tile-bar { background: var(--tile-bar); }
  .tile-cocktails { background: var(--tile-cocktails); }
  .tile-favorites { background: var(--tile-favorites); }
  .tile-shopping { background: var(--tile-shopping); }
  .tile-featured { background: var(--tile-featured); }
</style>
</head>
<body>
<main class="app-screen">
  <header class="app-header">
    <div class="header-button" aria-label="Home">
      <svg width="30" height="28" viewBox="0 0 30 28" fill="#ffffff">
        <path d="M15 2 L2 14 H6 V26 H12 V18 H18 V26 H24 V14 H28 Z"/>
      </svg>
    </div>
    <h1 class="app-title">Cocktail Search</h1>
    <div class="header-button" aria-label="Settings">
      <svg width="34" height="34" viewBox="0 0 34 34">
        <g fill="#ffffff">
          <circle cx="17" cy="17" r="11"/>
          <rect x="14" y="2" width="6" height="30" rx="1.5"/>
          <rect x="14" y="2" width="6" height="30" rx="1.5" transform="rotate(45 17 17)"/>
          <rect x="14" y="2" width="6" height="30" rx="1.5" transform="rotate(90 17 17)"/>
          <rect x="14" y="2" width="6" height="30" rx="1.5" transform="rotate(135 17 17)"/>
        </g>
        <circle cx="17" cy="17" r="5" fill="var(--header-top)"/>
      </svg>
    </div>
  </header>

  <p class="quote quote-intro">“ Lorem ipsum dolor sit amet ipsum dolor sit amet ipsum dolor sit amet ”</p>

  <nav class="menu-grid">
    <div class="menu-tile tile-shaker">
      <svg width="60" height="90" viewBox="0 0 60 90" fill="none" stroke="var(--icon-stroke)" stroke-width="3.5" stroke-linejoin="round">
        <rect x="23" y="3" width="14" height="10" rx="2"/>
        <path d="M18 13 H42 L44 28 H16 Z"/>
        <path d="M12 28 H48 L44 86 H16 Z"/>
        <path d="M15 44 H45"/>
      </svg>
      <span class="tile-label">Shaker</span>
    </div>
    <div class="menu-tile tile-bar">
      <svg width="110" height="90" viewBox="0 0 110 90" fill="none" stroke="var(--icon-stroke)" stroke-width="3.5" stroke-linejoin="round">
        <path d="M16 6 H24 V26 Q32 34 32 44 V86 H8 V44 Q8 34 16 26 Z"/>
        <path d="M46 6 H54 V26 Q62 34 62 44 V86 H38 V44 Q38 34 46 26 Z"/>
        <path d="M74 40 H104 Q104 64 89 66 Q74 64 74 40 Z"/>
        <path d="M76 52 H102"/>
        <path d="M89 66 V84 M80 86 H98"/>
      </svg>
      <span class="tile-label">My Bar</span>
    </div>
    <div class="menu-tile tile-cocktails">
      <svg width="80" height="96" viewBox="0 0 80 96" fill="none" stroke="var(--icon-stroke)" stroke-width="3.5" stroke-linejoin="round" stroke-linecap="round">
        <path d="M6 34 H66 L36 62 Z"/>
        <path d="M36 62 V88 M20 90 H52"/>
        <path d="M40 34 L58 8 Q62 2 68 6"/>
        <circle cx="22" cy="40" r="3" fill="var(--icon-stroke)"/>
      </svg>
      <span class="tile-label">Cocktails</span>
    </div>
    <div class="menu-tile tile-favorites">
      <svg width="72" height="90" viewBox="0 0 72 90" fill="none" stroke="var(--icon-stroke)" stroke-width="3.5" stroke-linejoin="round">
        <path d="M36 72 L10 46 Q2 36 8 26 Q16 14 28 18 Q34 20 36 26 Q38 20 44 18 Q56 14 64 26 Q70 36 62 46 Z"/>
      </svg>
      <span class="tile-label">Favorites</span>
    </div>
    <div class="menu-tile tile-shopping">
      <svg width="100" height="80" viewBox="0 0 100 80" fill="none" stroke="var(--icon-stroke)" stroke-width="4" stroke-linejoin="round" stroke-linecap="round">
        <path d="M4 10 H16 L28 50 H80"/>
        <path d="M20 20 H94 L82 46 H28"/>
        <circle cx="34" cy="64" r="6" fill="var(--icon-stroke)"/>
        <circle cx="74" cy="64" r="6" fill="var(--icon-stroke)"/>
      </svg>
      <span class="tile-label">Shopping List</span>
    </div>
    <div class="menu-tile tile-featured">
      <svg width="60" height="96" viewBox="0 0 60 96" fill="var(--icon-stroke)">
        <path d="M18 36 L6 84 L16 78 L22 90 L30 50 Z"/>
        <path d="M42 36 L54 84 L44 78 L38 90 L30 50 Z"/>
        <circle cx="30" cy="26" r="20"/>
        <circle cx="30" cy="26" r="13" fill="var(--tile-featured)"/>
        <path d="M30 17 L33 23 L39 24 L34.5 28 L36 34 L30 31 L24 34 L25.5 28 L21 24 L27 23 Z"/>
      </svg>
      <span class="tile-label">Featured</span>
    </div>
  </nav>

  <p class="quote quote-footer">“ The content can be adjusted related to the screen size - additional toolbars can be added if needed ”</p>
</main>
</body>
</html>
```